Newsletter Design/ Three different newsletters headers

We are the Company which delivers Effective Hiring Solutions through our offices in about 30 different countries.
We need to design 3 different newsletter headers.
All three headers belongs to the same professional group could have something in common, but not look identical.
The image of an existing weekly newsletter (Team Velkoris News) is attached but we want to refresh it and we are looking for innovative ideas.
Please take a time to have a look at our website http://www.velkoris-example.net/public/ to get an idea of its style as well, but we don't have to use its format.
The document of logo guideline with the color/font style is also attached.

Names and subjects of newsletters are:
• Team Velkoris News (weekly) and Team Velkoris News+ (monthly)
Subject:
Weekly information about internal competition results between offices worldwide.
Latest news from different offices.
Monthly newsletter will be extended by some more information, article relevant to service.
• Velkoris Technical Bulletin
Velkoris Technical Bulletin (System)
Subject:
Questions&Answers for people who works with a system
Updates in a system if any.
• Velkoris Executive Brief
Subject:
Monthly letter to office executives, mission/vision/ strategic goals/action plans/news/updates

Target Market(s)

all three newsletters are internal, goes to our offices worldwide.

Industry/Entity Type

It Company

Requirements
Must have
• We use QUANDA to make circulation of newsletters please see attached document with a program requirements (head pictures sizes etc.)

```html
<!DOCTYPE html>
<html lang="en">
<head>
<meta charset="utf-8">
<title>Velkoris Newsletter Headers</title>
<link href="https://fonts.googleapis.com/css2?family=Montserrat:wght@400;500;700;800&family=Cabin:wght@400;500&display=swap" rel="stylesheet">
<style>
  :root{
    --navy:#1f2252;
    --orange:#e8731c;
    --orange-soft:#f6c79c;
    --grey-bg:#ebebeb;
    --grey-line:#8c90ab;
    --white:#ffffff;
    --text-grey:#5a5a5a;
  }
  html,body{margin:0;padding:0;width:744px;height:1200px;overflow:hidden;background:var(--grey-bg);}
  .stage{position:relative;width:700px;height:1127px;transform:scale(1.0629);transform-origin:0 0;}
  .header{position:absolute;left:26px;width:648px;overflow:hidden;box-shadow:0 1px 3px rgba(0,0,0,.18);}
  .header svg.shapes{position:absolute;inset:0;width:100%;height:100%;}
  .news{top:44px;height:396px;background:var(--white);}
  .bulletin{top:478px;height:322px;background:var(--navy);}
  .brief{top:838px;height:255px;background:var(--white);}
  .brand{position:absolute;left:25px;font-family:"Montserrat",sans-serif;font-weight:700;letter-spacing:2px;margin:0;}
  .news .brand{top:24px;font-size:25px;color:var(--navy);}
  .bulletin .brand,.brief .brand{top:34px;font-size:19px;color:var(--white);}
  .title{position:absolute;left:25px;margin:0;font-family:"Montserrat",sans-serif;}
  .news .title{top:116px;font-size:39px;line-height:45px;font-weight:800;color:var(--navy);}
  .bulletin .title{top:130px;font-size:33px;line-height:45px;font-weight:400;color:var(--white);}
  .brief .title{top:104px;font-size:33px;line-height:47px;font-weight:400;color:var(--white);}
  .url{font-family:"Cabin",sans-serif;}
  .news .url{position:absolute;top:32px;right:54px;font-size:12px;color:var(--text-grey);}
  .tagline{font-family:"Cabin",sans-serif;color:var(--navy);margin:0;}
  .news .tagline{position:absolute;left:463px;top:350px;font-size:17px;}
  .tag-box{position:absolute;left:504px;top:276px;width:144px;height:34px;background:var(--white);text-align:center;}
  .tag-box .tagline{font-size:14px;line-height:18px;}
  .tag-box .url{display:block;font-size:10px;color:var(--white);background:var(--orange);line-height:14px;}
  .brief-tag{position:absolute;left:513px;top:20px;}
  .brief-tag .tagline{font-size:15px;}
  .brief-tag .url{display:block;font-size:11px;color:var(--orange);}
  .art{position:absolute;}
</style>
</head>
<body>
<div class="stage">

  <section class="header news">
    <svg class="shapes" viewBox="0 0 648 396" aria-hidden="true">
      <polygon points="410,40 648,40 648,396 235,396" fill="var(--orange)"/>
      <g stroke="#f08a3a" stroke-width="6">
        <line x1="455" y1="40" x2="290" y2="396"/><line x1="475" y1="40" x2="310" y2="396"/>
        <line x1="495" y1="40" x2="330" y2="396"/><line x1="515" y1="40" x2="350" y2="396"/>
      </g>
      <polygon points="600,52 636,0 648,0 648,52" fill="var(--navy)"/>
      <g stroke="var(--orange-soft)" stroke-width="3">
        <line x1="205" y1="293" x2="225" y2="254"/><line x1="215" y1="293" x2="235" y2="254"/>
        <line x1="225" y1="293" x2="245" y2="254"/><line x1="235" y1="293" x2="255" y2="254"/>
        <line x1="245" y1="293" x2="265" y2="254"/>
      </g>
      <polygon points="50,293 300,293 297,298 47,298" fill="var(--navy)"/>
      <polygon points="16,301 240,301 232,316 8,316" fill="var(--orange)"/>
    </svg>
    <div class="art" role="img" aria-label="Illustration of a team of helmeted figures pushing a wooden cart of barrels together" style="left:262px;top:160px;width:362px;height:175px;background:radial-gradient(ellipse at 60% 50%,rgba(60,70,140,.55),rgba(140,80,40,.35) 55%,rgba(232,115,28,0) 75%);"></div>
    <h2 class="brand">VELKORIS</h2>
    <span class="url">www.velkoris-example.com</span>
    <h1 class="title">TEAM<br>VELKORIS<br>NEWS</h1>
    <p class="tagline">Build Your Team</p>
  </section>

  <section class="header bulletin">
    <svg class="shapes" viewBox="0 0 648 322" aria-hidden="true">
      <polygon points="252,0 355,0 330,70" fill="var(--orange)"/>
      <polygon points="70,270 290,270 289,272 69,272" fill="var(--grey-line)"/>
      <polygon points="18,274 284,274 274,297 8,297" fill="var(--orange)"/>
      <g stroke="var(--orange)" stroke-width="3">
        <line x1="286" y1="297" x2="296" y2="274"/><line x1="294" y1="297" x2="304" y2="274"/>
        <line x1="302" y1="297" x2="312" y2="274"/><line x1="310" y1="297" x2="320" y2="274"/>
        <line x1="318" y1="297" x2="328" y2="274"/>
      </g>
    </svg>
    <div class="art" role="img" aria-label="Photo collage of smiling business people and documents with charts" style="left:330px;top:0;width:318px;height:322px;clip-path:polygon(22px 0,318px 0,318px 322px,105px 322px,22px 150px);background:linear-gradient(135deg,#dfe3ea,#b9c2d4 35%,#e9e3dc 60%,#c6ccd8);"></div>
    <svg class="shapes" viewBox="0 0 648 322" aria-hidden="true">
      <g stroke="var(--white)" stroke-width="3">
        <line x1="437" y1="0" x2="437" y2="322"/><line x1="546" y1="0" x2="546" y2="322"/>
        <line x1="437" y1="105" x2="546" y2="105"/><line x1="546" y1="215" x2="648" y2="215"/>
      </g>
    </svg>
    <h2 class="brand">VELKORIS</h2>
    <h1 class="title">VELKORIS<br>TECHNICAL<br>BULLETIN</h1>
    <div class="tag-box">
      <p class="tagline">Build Your Team</p>
      <span class="url">www.velkoris-example.com</span>
    </div>
  </section>

  <section class="header brief">
    <svg class="shapes" viewBox="0 0 648 255" aria-hidden="true">
      <polygon points="0,0 340,0 478,255 0,255" fill="var(--navy)"/>
      <g stroke-width="2.5">
        <line x1="348" y1="0" x2="486" y2="255" stroke="#2d3160"/>
        <line x1="356" y1="0" x2="494" y2="255" stroke="#3e4270"/>
        <line x1="364" y1="0" x2="502" y2="255" stroke="#525682"/>
        <line x1="372" y1="0" x2="510" y2="255" stroke="#676b94"/>
        <line x1="380" y1="0" x2="518" y2="255" stroke="#7e82a6"/>
        <line x1="388" y1="0" x2="526" y2="255" stroke="#989bb8"/>
        <line x1="396" y1="0" x2="534" y2="255" stroke="#b4b6cb"/>
        <line x1="404" y1="0" x2="542" y2="255" stroke="#d0d1de"/>
      </g>
      <polygon points="10,202 290,202 282,219 0,219 0,202" fill="var(--orange)"/>
      <g stroke="var(--orange)" stroke-width="3">
        <line x1="290" y1="219" x2="298" y2="202"/><line x1="298" y1="219" x2="306" y2="202"/>
        <line x1="306" y1="219" x2="314" y2="202"/>
      </g>
      <line x1="315" y1="216" x2="358" y2="216" stroke="var(--grey-line)" stroke-width="2"/>
      <line x1="135" y1="228" x2="350" y2="228" stroke="var(--grey-line)" stroke-width="2"/>
    </svg>
    <div class="art" role="img" aria-label="Faint decorative pattern in soft grey and peach tones" style="left:470px;top:80px;width:178px;height:175px;background:radial-gradient(circle at 65% 70%,rgba(246,199,156,.45),rgba(200,203,220,.35) 45%,rgba(255,255,255,0) 75%);"></div>
    <h2 class="brand">VELKORIS</h2>
    <h1 class="title">VELKORIS<br>EXECUTIVE BRIEF</h1>
    <div class="brief-tag">
      <p class="tagline">Build Your Team</p>
      <span class="url">www.velkoris-example.com</span>
    </div>
  </section>

</div>
</body>
</html>
```